website design + images

We need a very appealing website design, layout and images for a sales analytics and sales productivity services company based in San Ramon, California. We need a good design for the home page and a template for all other pages (total 2 designs), and images for all inner pages (center column/banner images, and right hand top corner small images). There are about 18 inner pages.
Updates

Our existing website is www.brightvale.com
Our corporate colours are the ones that are there on the website. The logo is also shown. We will be changing the tagline to "accelerating revenue" or equivalent of that.

Please use the document "website for brightvale - template v2.doc" that I just uploaded for any reference to the content, navigation and wireframes. A few more clarifications are provided mainly for the link "Solutions".

Rajesh Kothuri

Hi,
We just uploaded ver 4 of the website template. There is more elaboration provided around the sublinks / sections for Solutions. Pls review and do get back if you need any clarifications.

Rgds
Rajesh Kothuri

Hi all,
We have so far received a few good designs. The designs are more or less on the right track. I would like to urge all of you to use the content and navigation provided in the document attached to our brief "website for brightvale - template v4.doc".  Please DO NOT use the content in our existing website www.brightvale.com . That is very old. We mentioned it only for reference to colour theme and broad details.

We have totally 13 sections in Solutions pages. They may be designed as a tree of links - first level sublinks - second level sublinks or links - first level sublinks and the remaining as sections within the first level sublinks pages. The page design would remain the same for all inner pages except careers. But after finalizing the design for the inner page, we will need images for the different inner pages.

Rgds
Rajesh Kothuri

Hi,
Thank you all for participation and very good designs. We are quite happy with what we have seen. We have now shortlisted about 4 vendors and sending invididual feedback to them for further improvement. We will be finalizing by Monday or Tuesday.  To the vendors who do not get feedback from us, thank you very much for participation. We may still do business in future for some of our other needs. 
The following are the process steps / expectations going forward, 
1. Feedback to the shortlisted designers and inviting improvements.
2. Review of the improved designs and further shortlist & feedback or direct finalization.
3. The design should be in 1024*768
2. Number of page designs = 2 (home page, inner page).
4. Home page design: instead of delivery model and customers, show one link "Why Us".
4. Solutions page design:  We will be needing an image in center column of solutions page that in a nutshell gives all the different types of solutions we provide. The entire set of solutions is in our attached document website for brightvale - template v4 and I am just uploading v5 with more description on sublinks.
5. After selection, we will be needing images for all the solution pages (total 12 pages under solutions + one solutions page), 1 image for Why Us?, 1 for Careers, and 3 for company (about us/ team, core values, ...) = total 18

Rgds
Rajesh Kothuri

Target Market(s)

We are a sales analytics and sales productivity services company. We help B2B companies with: sales planning; sales operations and sales measurement. The characteristics of our customers are:
- B2B medium enterprises (USD 100M- USD 2B in revenue) in the US
- Primary target verticals are: high-tech, engineering and professional services firms
- Our primary target customers titles are VP of Sales or VP of marketing; we could be selling to the CEO at companies with revenues below $200M

Industry/Entity Type

Consulting

Requirements
Must have
• - Clean, uncluttered design
• - Easy navigation; minimum clicks
Nice to have
• We have already built a content management system and wireframes for this site. To the extent possible, it would be great to leverage the wireframe structure we built, provided you don’t have to compromise on the look and feel and navigation of the site. Below is what we currently have as banner sizes and resolutions are:
• Home page banner size: 950 * 250’
• All pages – center top - image size: 558 * 160
• All pages – right hand top image – 175*135’

```html
<!DOCTYPE html>
<html lang="en">
<head>
<meta charset="utf-8">
<title>Brightvale – Home</title>
<link href="https://fonts.googleapis.com/css2?family=Noto+Sans:wght@400;600&family=PT+Sans:wght@400;700&display=swap" rel="stylesheet">
<style>
  :root {
    --page-bg: #f6f6f6;
    --header-top: #ffffff;
    --header-bottom: #e9e9e9;
    --band-light: #9ccaf1;
    --band-dark: #2f7bcb;
    --brand-teal: #17a8a8;
    --brand-navy: #1c2a5a;
    --ink: #222222;
    --muted: #666666;
    --link: #1e3f8a;
    --panel-border: #c9c9c9;
    --card-border: #d6d6d6;
    --managed: #2b3590;
    --consulting: #e2661f;
    --staffing: #5a9a3a;
    --footer-light: #a9d0f4;
    --footer-dark: #7db3ea;
  }
  * { box-sizing: border-box; margin: 0; padding: 0; }
  html, body { width: 1200px; height: 631px; overflow: hidden; }
  body {
    position: relative;
    background: var(--page-bg);
    font-family: "Noto Sans", Verdana, sans-serif;
    color: var(--ink);
  }
  .header {
    position: absolute; left: 0; top: 0; width: 1200px; height: 77px;
    background: linear-gradient(var(--header-top), var(--header-bottom));
  }
  .brand {
    position: absolute; left: 222px; top: 22px;
    display: flex; align-items: center; gap: 8px;
    font-family: "PT Sans", sans-serif; font-size: 26px; font-weight: 400;
    color: var(--brand-navy); letter-spacing: 1px;
  }
  .brand-dot { width: 14px; height: 14px; border-radius: 50%; background: var(--brand-teal); }
  .utility-links {
    position: absolute; right: 209px; top: 5px;
    font-size: 10.5px; color: var(--brand-navy);
  }
  .utility-links a { color: var(--brand-navy); text-decoration: none; }
  .main-nav { position: absolute; left: 417px; top: 49px; display: flex; gap: 2px; }
  .main-nav a {
    display: block; height: 26px; line-height: 26px; text-align: center;
    background: linear-gradient(#fbfbfb, #e4e4e4);
    border: 1px solid #d4d4d4; border-bottom: none;
    font-family: "PT Sans", sans-serif; font-size: 13.5px; color: var(--brand-navy);
    text-decoration: none;
  }
  .main-nav a.is-active { color: #1f5fae; }
  .hero-band {
    position: absolute; left: 0; top: 77px; width: 1200px; height: 195px;
    background: linear-gradient(var(--band-light), var(--band-dark));
  }
  .hero {
    position: absolute; left: 204px; top: 77px; width: 792px; height: 195px;
    border-radius: 0 0 6px 6px; overflow: hidden;
    background: linear-gradient(180deg, #b9dbf7 0%, #e6f2fc 70%, #ffffff 100%);
  }
  .hero-photo {
    position: absolute; left: 0; top: 0; width: 230px; height: 195px;
    background: linear-gradient(135deg, #e8e6e0, #d6cbb6 55%, #f2efe9);
  }
  .hero-card {
    position: absolute; left: 269px; top: 26px; width: 459px; height: 133px;
    background: #ffffff; border-radius: 8px; box-shadow: 0 1px 4px rgba(0,0,0,.15);
    padding: 14px 18px;
  }
  .hero-title { font-family: "PT Sans", sans-serif; font-size: 19px; font-weight: 700; color: #555; }
  .hero-title span { color: var(--brand-teal); }
  .hero-text { margin: 6px 0 0 19px; font-size: 10.3px; line-height: 15px; color: var(--muted); }
  .slide-dots { position: absolute; right: 17px; top: 173px; display: flex; gap: 5px; }
  .slide-dots span {
    width: 13px; height: 13px; border-radius: 50%; border: 1px solid #6aa8e0;
    background: #ffffff; font-size: 8px; line-height: 11px; text-align: center; color: #334;
  }
  .content-panel {
    position: absolute; left: 204px; top: 286px; width: 792px; height: 239px;
    border: 1px solid var(--panel-border); border-radius: 4px; background: #ffffff;
  }
  .card {
    position: absolute; top: 8px; height: 219px;
    border: 1px solid var(--card-border); border-radius: 3px; background: #fcfcfc;
    padding: 10px 7px 0 8px;
  }
  .card h2 {
    font-family: "PT Sans", sans-serif; font-size: 15px; font-weight: 700; height: 22px;
    display: flex; align-items: center; gap: 6px;
  }
  .card h2.plain { font-weight: 400; }
  .card h2 .mark { width: 4px; height: 13px; display: inline-block; }
  .card p { font-size: 10.3px; line-height: 14.5px; color: var(--muted); }
  .card p.justified { text-align: justify; margin-top: 2px; }
  .card .thumb {
    width: 139px; height: 80px; border-radius: 5px; border: 1px solid #ddd; margin: 4px 0 12px -1px;
  }
  .card .more {
    position: absolute; right: 7px; bottom: 5px; font-size: 10.5px; color: var(--link); text-decoration: none;
  }
  .quote { margin-top: 2px; text-align: justify; }
  .quote-by { text-align: right; font-size: 10.3px; color: var(--ink); margin: 2px 0 6px; }
  .footer-band {
    position: absolute; left: 0; top: 533px; width: 1200px; height: 67px;
    background: linear-gradient(var(--footer-light), var(--footer-dark));
    border-radius: 4px;
    text-align: center; line-height: 67px; font-size: 10.5px; color: var(--ink);
  }
  .footer-band a { color: var(--ink); text-decoration: none; }
</style>
</head>
<body>
  <header class="header">
    <div class="brand"><span class="brand-dot"></span>Brightvale</div>
    <div class="utility-links"><a href="#">Sign in</a> | <a href="#">Contact us</a> | <a href="#">Sitemap</a></div>
    <nav class="main-nav">
      <a href="#" class="is-active" style="width:88px">Home</a>
      <a href="#" style="width:89px">Solutions</a>
      <a href="#" style="width:121px">Delivery Model</a>
      <a href="#" style="width:89px">Customers</a>
      <a href="#" style="width:89px">Company</a>
      <a href="#" style="width:89px">Careers</a>
    </nav>
  </header>

  <div class="hero-band"></div>
  <section class="hero">
    <div class="hero-photo" role="img" aria-label="Photo of a smiling businesswoman seated in a bright office"></div>
    <div class="hero-card">
      <h1 class="hero-title"><span>Brightvale</span> is a marketing and sales</h1>
      <p class="hero-text">Lorem Ipsum is simply dummy text of the printing and typesetting industry. Lorem Ipsum has been the industry's standard dummy text ever since the 1500s, when an unknown printer took a galley of type and scrambled it to make a type specimen book. It has survived not only five centuries,</p>
    </div>
    <div class="slide-dots"><span>1</span><span>2</span><span>3</span></div>
  </section>

  <main class="content-panel">
    <article class="card" style="left:6px;width:148px">
      <h2 style="color:var(--brand-teal)">Welcome</h2>
      <p class="justified">Lorem Ipsum is simply dummy text of the printing and typesetting industry. Lorem Ipsum has been the industry's standard dummy text ever since the 1500s, when an unknown printer took a galley of type and</p>
      <a class="more" href="#">Read more...</a>
    </article>

    <article class="card" style="left:159px;width:153px">
      <h2 class="plain" style="color:var(--managed)"><span class="mark" style="background:var(--managed)"></span>Mnaged Services</h2>
      <div class="thumb" role="img" aria-label="Photo of a young businessman in a suit" style="background:linear-gradient(135deg,#f4f4f6,#c9c6d8)"></div>
      <p>Brightvale manages entire processes in mar-keting and sales opera-tions with software and services. Pay as you go.</p>
      <a class="more" href="#">Read more...</a>
    </article>

    <article class="card" style="left:317px;width:153px">
      <h2 class="plain" style="color:var(--consulting)"><span class="mark" style="background:var(--consulting)"></span>Consulting</h2>
      <div class="thumb" role="img" aria-label="Photo of a consultant wearing a headset" style="background:linear-gradient(135deg,#ededed,#cfcfcf)"></div>
      <p>Brightvale delivers cus-tomized solutions to address your biggest marketing and sales operations challenges.</p>
      <a class="more" href="#">Read more...</a>
    </article>

    <article class="card" style="left:476px;width:152px">
      <h2 class="plain" style="color:var(--staffing)"><span class="mark" style="background:var(--staffing)"></span>Contract Staffing</h2>
      <div class="thumb" role="img" aria-label="Photo of a team of business professionals" style="background:linear-gradient(135deg,#e9ece8,#9fa6a2)"></div>
      <p>Access Brightvale's broad pool of manage-ment, business, and IT talent for your contract staffing needs.</p>
      <a class="more" href="#">Read more...</a>
    </article>

    <article class="card" style="left:635px;width:149px">
      <h2 style="color:var(--brand-teal)">Testimonial</h2>
      <p class="quote">“Lorem Ipsum is simply dummy text f the printing and typesetting the is industry. ”</p>
      <p class="quote-by">- Marian Holloway</p>
      <p class="quote">“Lorem Ipsum is simply dummy text f the printing and typesetting the is industry. ”</p>
      <p class="quote-by">- Marian Holloway</p>
      <a class="more" href="#">Read more...</a>
    </article>
  </main>

  <footer class="footer-band">© 2010 Brightvale, Inc. | <a href="#">Contact Us</a> | <a href="#">Sign in (register)</a> | <a href="#">Contact us</a> | <a href="#">Sitemap</a></footer>
</body>
</html>
```